Book for new dads needs a cover.

We need a cover for a book titled Roadmap to Early Parenthood: Practical Methods for Welcoming a Newborn, Juggling Career and Home Life, and Managing Mental Health on the Path to Becoming a Parent. We would like to see a design that emphasizes healthy babies and confident dads.

```html
<!DOCTYPE html>
<html lang="en">
<head>
<meta charset="utf-8">
<title>Roadmap to Early Parenthood – Book Cover</title>
<link rel="stylesheet" href="https://fonts.googleapis.com/css2?family=Archivo:ital,wght@0,700;0,800;0,900;1,400&display=swap">
<style>
  :root {
    --backdrop: #262626;
    --paper: #ffffff;
    --ink: #111111;
    --title-orange: #ff3d00;
    --title-blue: #0561b8;
    --tag-yellow: #fff700;
    --photo-hair: #5a3f2e;
    --photo-skin: #d6a283;
    --photo-shirt: #ebe7e3;
  }
  * { margin: 0; padding: 0; box-sizing: border-box; }
  html, body {
    width: 1200px;
    height: 1200px;
    overflow: hidden;
    background: var(--backdrop);
  }
  .cover {
    position: absolute;
    left: 216px;
    top: 25px;
    width: 767px;
    height: 1150px;
    background: var(--paper);
    overflow: hidden;
    font-family: "Archivo", Arial, sans-serif;
  }
  .author {
    position: absolute;
    top: 50px;
    left: 0;
    width: 100%;
    display: flex;
    align-items: center;
    justify-content: center;
    gap: 14px;
  }
  .author-rule {
    width: 190px;
    height: 2px;
    background: var(--ink);
  }
  .author-name {
    font-weight: 800;
    font-size: 31px;
    letter-spacing: -1px;
    color: var(--ink);
    line-height: 1;
  }
  .title-art {
    position: absolute;
    left: 0;
    top: 0;
    width: 767px;
    height: 500px;
  }
  .title-word {
    font-family: "Archivo", Arial, sans-serif;
    font-weight: 900;
  }
  .title-top { fill: var(--title-orange); }
  .title-bottom { fill: var(--title-blue); }
  .tag-box { fill: var(--tag-yellow); }
  .tag-text {
    fill: var(--title-blue);
    font-family: "Archivo", Arial, sans-serif;
    font-weight: 800;
  }
  .subtitle {
    position: absolute;
    top: 472px;
    left: 0;
    width: 100%;
    text-align: center;
  }
  .subtitle-lead {
    font-weight: 800;
    font-size: 25px;
    color: var(--title-orange);
    letter-spacing: 0.2px;
    line-height: 1.2;
  }
  .subtitle-rest {
    margin-top: 4px;
    font-style: italic;
    font-weight: 400;
    font-size: 20px;
    line-height: 1.45;
    color: var(--ink);
  }
  .hero-photo {
    position: absolute;
    left: 88px;
    top: 572px;
    width: 610px;
    height: 578px;
    border-radius: 260px 260px 0 0;
    background: linear-gradient(180deg,
      var(--photo-hair) 0%,
      var(--photo-hair) 14%,
      var(--photo-skin) 34%,
      var(--photo-skin) 58%,
      var(--photo-shirt) 74%,
      var(--photo-shirt) 100%);
  }
</style>
</head>
<body>
  <main class="cover">
    <div class="author">
      <span class="author-rule"></span>
      <span class="author-name">AUTHOR NAME</span>
      <span class="author-rule"></span>
    </div>

    <svg class="title-art" viewBox="0 0 767 500" aria-label="Roadmap to Early Parenthood">
      <text class="title-word title-top" x="42" y="230" font-size="150" textLength="685" lengthAdjust="spacingAndGlyphs">ROADMAP</text>
      <text class="title-word title-bottom" x="23" y="455" font-size="200" textLength="724" lengthAdjust="spacingAndGlyphs">PARENTHOOD</text>
      <g transform="rotate(-3 500 280)">
        <rect class="tag-box" x="200" y="222" width="378" height="86" rx="6"/>
        <text class="tag-text" x="389" y="280" font-size="42" text-anchor="middle">TO EARLY</text>
      </g>
    </svg>

    <section class="subtitle">
      <p class="subtitle-lead">PRACTICAL METHODS FOR WELCOMING</p>
      <p class="subtitle-rest">a Newborn, Juggling Career and Home Life, and Managing<br>Mental Health on the Path to Becoming a Parent.</p>
    </section>

    <div class="hero-photo" role="img" aria-label="Photo of a smiling father in a white T-shirt gently holding his newborn baby close to his face"></div>
  </main>
</body>
</html>
```